Calvanto Group Real Estate Company business cards

New business card design, we are generally happy with the basic layout of the existing front of business card, (feel free to change) but require a head shot photo on the back side.

http://www.calvanto.com.au/

Attached logos, and existing business card

------------------------------

Target Market(s)

Real estate

Industry/Entity Type

Real Estate

Contact Information for Business Card

Standard size double sided

Font styles to use
Other font styles liked:
• Futura

Requirements
Must have
• Photo head shot on the back side
Nice to have
• yes
Should not have
• No

```html
<!DOCTYPE html>
<html lang="en">
<head>
<meta charset="utf-8">
<title>Calvanto Group – Business Cards</title>
<link rel="stylesheet" href="https://fonts.googleapis.com/css2?family=Jost:wght@400;500;600&display=swap">
<style>
  :root {
    --purple: #35286e;
    --orange: #f7941d;
    --grey: #8a8a94;
    --ink: #2a2a33;
    --paper: #ffffff;
    --backdrop: #e9e8ee;
    --photo-tone: linear-gradient(160deg, #dfe2ea 0%, #c2c8d8 55%, #2f3a5c 100%);
  }
  * { box-sizing: border-box; margin: 0; padding: 0; }
  html, body { width: 1200px; height: 676px; overflow: hidden; }
  body {
    background: var(--backdrop);
    font-family: "Jost", "Futura", sans-serif;
    color: var(--ink);
    display: flex;
    align-items: center;
    justify-content: center;
    gap: 60px;
  }
  .card {
    position: relative;
    width: 520px;
    height: 297px;
    background: var(--paper);
    box-shadow: 0 6px 18px rgba(40, 30, 80, 0.18);
    overflow: hidden;
  }
  .brand-name {
    font-family: "Jost", "Futura", sans-serif;
    font-weight: 500;
    color: var(--purple);
    letter-spacing: 0.5px;
    line-height: 1;
    white-space: nowrap;
  }

  /* Contact side */
  .card--contact .brand-name {
    position: absolute;
    top: 38px;
    left: 0;
    right: 0;
    text-align: center;
    font-size: 38px;
  }
  .rule {
    position: absolute;
    top: 128px;
    left: 40px;
    right: 40px;
    height: 1px;
    background: var(--purple);
  }
  .contact-list {
    position: absolute;
    top: 146px;
    left: 40px;
    list-style: none;
    font-size: 13px;
    line-height: 1.55;
    color: var(--ink);
  }
  .contact-list li { display: flex; align-items: center; gap: 8px; }
  .contact-list svg { width: 11px; height: 11px; fill: var(--purple); flex: none; }
  .person {
    position: absolute;
    top: 150px;
    right: 40px;
    text-align: right;
  }
  .person__name { font-size: 16px; font-weight: 600; color: var(--purple); }
  .person__role { font-size: 12px; color: var(--ink); }
  .company {
    position: absolute;
    top: 212px;
    right: 40px;
    text-align: right;
    font-size: 12px;
    line-height: 1.3;
  }
  .bands { position: absolute; left: 0; bottom: 0; width: 520px; height: 48px; }

  /* Photo side */
  .card--photo .brand-name {
    position: absolute;
    top: 50px;
    left: 36px;
    font-size: 34px;
  }
  .services {
    position: absolute;
    top: 118px;
    left: 40px;
    font-size: 13px;
    font-weight: 500;
    letter-spacing: 1px;
    color: var(--ink);
  }
  .headshot {
    position: absolute;
    right: 16px;
    bottom: 0;
    width: 190px;
    height: 220px;
    background: var(--photo-tone);
  }
</style>
</head>
<body>

  <section class="card card--contact" aria-label="Business card contact side">
    <p class="brand-name">Calvanto Group</p>
    <div class="rule"></div>
    <ul class="contact-list">
      <li>
        <svg viewBox="0 0 12 12" aria-hidden="true"><rect x="3" y="0.5" width="6" height="11" rx="1.2"/></svg>
        0412 555 208
      </li>
      <li>
        <svg viewBox="0 0 12 12" aria-hidden="true"><path d="M0 2h12v8H0z"/></svg>
        daniel.tran@calvanto.com.au
      </li>
      <li>
        <svg viewBox="0 0 12 12" aria-hidden="true"><circle cx="6" cy="6" r="5.5"/></svg>
        www.calvanto.com.au
      </li>
    </ul>
    <div class="person">
      <p class="person__name">Daniel Tran</p>
      <p class="person__role">Director</p>
    </div>
    <div class="company">
      <p>Calvanto Group</p>
      <p>ABN: 12 345 678 901</p>
    </div>
    <svg class="bands" viewBox="0 0 520 48" aria-hidden="true">
      <rect x="0" y="6" width="340" height="12" fill="var(--purple)"/>
      <polygon points="320,18 520,18 520,48 300,48" fill="var(--orange)"/>
    </svg>
  </section>

  <section class="card card--photo" aria-label="Business card photo side">
    <p class="brand-name">Calvanto Group</p>
    <p class="services">BUY | SELL | RENT</p>
    <div class="headshot" role="img" aria-label="Head shot photo of the director in a navy suit and blue tie"></div>
  </section>

</body>
</html>
```